Haulage company, lets use ruby red white and some 3rd color for web design. and Garvel Pryce Transport logo

Target Market(s)

Transport industry

Industry/Entity Type

transport

Number of Pages Required

2 page

Requirements
Must have
• Logo

```html
<!DOCTYPE html>
<html lang="en">
<head>
<meta charset="utf-8">
<title>Garvel Pryce Transport</title>
<link rel="stylesheet" href="https://fonts.googleapis.com/css2?family=Poppins:wght@400;500;600;700;800&display=swap">
<style>
:root{
  --ruby:#e2135b;
  --ruby-dark:#b70e49;
  --ink:#1a1a1a;
  --text:#333;
  --muted:#666;
  --grey-bg:#f1f1f1;
  --field:#efefef;
  --white:#fff;
  --black:#0b0b0b;
}
*{box-sizing:border-box;margin:0;padding:0}
html,body{width:1200px;height:3848px;overflow:hidden}
body{font-family:"Poppins",sans-serif;color:var(--text);background:var(--white);position:relative}
.btn{display:inline-flex;align-items:center;gap:8px;background:var(--ruby);color:var(--white);font-weight:600;font-size:14px;letter-spacing:.5px;padding:12px 26px;border-radius:30px;text-transform:uppercase}
.btn svg{width:14px;height:14px}
.section-title{color:var(--ruby);font-weight:700;font-size:32px;text-align:center;text-transform:uppercase}
.body-copy{font-size:15px;line-height:26px;color:var(--text)}

/* header */
.site-header{position:absolute;top:0;left:0;width:1200px;height:150px;background:var(--white)}
.brand{position:absolute;left:40px;top:58px;color:var(--ruby);font-weight:700;font-size:24px}
.topbar{position:absolute;left:395px;top:30px;display:flex;gap:150px;font-size:14px;color:var(--ink)}
.topbar span{display:flex;align-items:center;gap:12px}
.topbar i{width:32px;height:32px;border-radius:50%;background:var(--ruby);display:flex;align-items:center;justify-content:center}
.topbar i svg{width:16px;height:16px}
.main-nav{position:absolute;left:360px;top:95px;display:flex;gap:34px;font-size:15px;font-weight:500;color:var(--ink)}
.main-nav a{color:inherit;text-decoration:none;padding-bottom:10px}
.main-nav a.active{border-bottom:3px solid var(--ruby)}
.nav-rule{position:absolute;left:360px;top:128px;width:690px;height:1px;background:#ddd}

/* hero */
.hero{position:absolute;top:150px;left:0;width:1200px;height:560px;overflow:hidden}
.hero-photo{position:absolute;inset:0;background:linear-gradient(180deg,#2a2c30 0%,#4b4c50 45%,#3a3634 75%,#1c1a19 100%)}
.hero-copy{position:absolute;top:210px;width:100%;text-align:center;color:var(--white)}
.hero-copy h1{font-size:44px;font-weight:800;line-height:54px;text-transform:uppercase}
.hero-copy p{font-size:22px;font-weight:500;margin:22px 0 30px}
.hero-wedge{position:absolute;left:0;bottom:0;width:1200px;height:60px}

/* services */
.services{position:absolute;top:860px;left:0;width:1200px}
.cards{position:absolute;top:90px;left:100px;display:flex;gap:35px}
.card{width:320px;height:380px;background:var(--white);box-shadow:0 4px 18px rgba(0,0,0,.14);text-align:center;padding-top:28px}
.card .icon{width:120px;height:120px;border-radius:50%;background:var(--ruby);margin:0 auto;display:flex;align-items:center;justify-content:center}
.card .icon svg{width:64px;height:64px}
.card h3{font-size:20px;font-weight:600;color:var(--ink);margin:28px 0 10px}
.card p{font-size:14px;line-height:22px;color:var(--muted);padding:0 30px}
.card a{display:inline-block;margin-top:14px;color:var(--ruby);font-weight:700;font-size:17px;text-decoration:underline}

/* about */
.about{position:absolute;top:1440px;left:0;width:1200px;height:530px;background:var(--grey-bg)}
.about-copy{position:absolute;left:100px;top:70px;width:500px}
.about h2,.what-we-do h2{color:var(--ruby);font-size:30px;font-weight:700;text-transform:uppercase;margin-bottom:14px}
.about .body-copy+.body-copy{margin-top:14px}
.about .btn{margin-top:24px}
.about-photo{position:absolute;left:660px;top:0;width:540px;height:530px}

/* what we do */
.what-we-do{position:absolute;top:2050px;left:0;width:1200px;height:510px}
.wwd-frame{position:absolute;left:110px;top:30px;width:420px;height:420px;border-right:4px solid var(--ruby);border-bottom:4px solid var(--ruby);border-radius:0 0 60px 0}
.wwd-photo{position:absolute;left:100px;top:0;width:410px;height:410px;background:linear-gradient(180deg,#c4ced6 0%,#dfe4e8 40%,#8b2a3d 62%,#9aa3a8 80%,#6f7478 100%)}
.wwd-copy{position:absolute;left:630px;top:40px;width:470px}
.wwd-copy .btn{margin-top:26px}

/* where we serve */
.serve{position:absolute;top:2560px;left:0;width:1200px;height:550px;background:var(--ruby);color:var(--white)}
.serve h2{position:absolute;left:100px;top:130px;font-size:30px;font-weight:700;text-transform:uppercase}
.serve-list{position:absolute;left:100px;top:190px;display:grid;grid-template-columns:200px 200px;row-gap:14px;font-size:19px;font-weight:500}
.serve-list li{list-style:none;display:flex;align-items:center;gap:8px}
.serve-list svg{width:16px;height:20px}
.serve-map{position:absolute;left:540px;top:110px;width:570px;height:340px;background:linear-gradient(180deg,rgba(255,255,255,.92),rgba(255,255,255,.82));border-radius:40% 30% 45% 35%/35% 40% 30% 45%}

/* contact */
.contact{position:absolute;top:3180px;left:0;width:1200px;height:400px}
.contact-form{position:absolute;left:220px;top:80px;width:760px;height:220px}
.field{position:absolute;left:0;width:370px;height:56px;background:var(--field);border-radius:10px;font-size:12px;color:#888;padding:16px 18px}
.field.message{left:385px;top:0;width:375px;height:200px}
.contact .btn{position:absolute;left:528px;top:310px}

/* footer */
.site-footer{position:absolute;top:3620px;left:0;width:1200px;height:228px;background:var(--black);color:var(--white);text-align:center}
.footer-brand{color:var(--ruby);font-weight:700;font-size:26px;margin-top:50px}
.footer-nav{display:flex;justify-content:center;gap:30px;font-size:14px;margin-top:28px}
.footer-rule{width:720px;height:1px;background:#444;margin:20px auto 18px}
.footer-copy{font-size:13px;color:#ccc}
</style>
</head>
<body>

<header class="site-header">
  <div class="brand">Garvel Pryce Transport</div>
  <div class="topbar">
    <span><i><svg viewBox="0 0 24 24" fill="#fff"><path d="M2 5h20v14H2z" opacity=".0"/><path d="M3 6h18v12H3zM3 6l9 7 9-7" fill="none" stroke="#fff" stroke-width="2"/></svg></i>info@garvelprycetransport.com</span>
    <span><i><svg viewBox="0 0 24 24"><path d="M6 3l4 4-2 3c1 2 4 5 6 6l3-2 4 4-3 3C10 21 3 14 3 6z" fill="#fff"/></svg></i>+1 555 014 2270</span>
  </div>
  <nav class="main-nav">
    <a class="active">Home</a><a>About Us</a><a>Services</a><a>What We Do</a><a>Testimonials</a><a>Gallery</a><a>Contact</a>
  </nav>
  <div class="nav-rule"></div>
</header>

<section class="hero">
  <div class="hero-photo" role="img" aria-label="Two white articulated haulage lorries parked at a depot at dusk"></div>
  <div class="hero-copy">
    <h1>Welcome to<br>Garvel Pryce Transport</h1>
    <p>Transport Logistics &amp; Supplies LTD</p>
    <span class="btn">Get Started <svg viewBox="0 0 16 16"><circle cx="8" cy="8" r="7" fill="#fff"/><path d="M6 4l4 4-4 4" stroke="#e2135b" stroke-width="2" fill="none"/></svg></span>
  </div>
  <svg class="hero-wedge" viewBox="0 0 1200 60" preserveAspectRatio="none">
    <polygon points="0,60 0,10 600,60" fill="#e2135b"/>
    <polygon points="0,60 0,30 600,60 1200,0 1200,60" fill="#fff"/>
  </svg>
</section>

<section class="services">
  <h2 class="section-title">Services</h2>
  <div class="cards">
    <div class="card">
      <div class="icon"><svg viewBox="0 0 64 64" fill="#fff"><rect x="4" y="18" width="36" height="24" rx="2"/><path d="M42 26h10l8 9v7H42z"/><circle cx="14" cy="46" r="5"/><circle cx="50" cy="46" r="5"/></svg></div>
      <h3>Bulk Haulage</h3>
      <p>Lorem ipsum dolor sit amet, sed do tempor incididunt ut labore et dolore magna aliqua.</p>
      <a>Read More</a>
    </div>
    <div class="card">
      <div class="icon"><svg viewBox="0 0 64 64" fill="#fff"><path d="M6 20l30 6-4 14H6z"/><path d="M38 28h10l8 8v6H36z"/><circle cx="16" cy="46" r="5"/><circle cx="48" cy="46" r="5"/></svg></div>
      <h3>Tippers</h3>
      <p>Lorem ipsum dolor sit amet, sed do tempor incididunt ut labore et dolore magna aliqua.</p>
      <a>Read More</a>
    </div>
    <div class="card">
      <div class="icon"><svg viewBox="0 0 64 64" fill="none" stroke="#fff" stroke-width="3"><path d="M32 44V20"/><path d="M32 30c-8 0-12-6-12-12 8 0 12 6 12 12zM32 26c8 0 12-6 12-12-8 0-12 6-12 12z"/><path d="M10 40c6 0 10 6 22 6s14-6 22-6"/></svg></div>
      <h3>Agricultural Goods Haulage</h3>
      <p>Lorem ipsum dolor sit amet, sed do tempor incididunt ut labore et dolore magna aliqua.</p>
      <a>Read More</a>
    </div>
  </div>
</section>

<section class="about">
  <div class="about-copy">
    <h2>About Garvel Pryce Transport</h2>
    <p class="body-copy">Lorem ipsum dolor sit amet, consectetur adipiscing elit, sed do eiusmod tempor incididunt ut labore et dolore magna aliqua. Quis ipsum suspendisse ultrices gravida. Risus commodo viverra maecenas accumsan lacus vel facilisis.</p>
    <p class="body-copy">Sed ut perspiciatis unde omnis iste natus error sit voluptatem accusantium doloremque laudantium, totam rem aperiam, eaque ipsa quae ab illo inventore veritatis et quasi architecto beatae vitae dicta sunt explicabo. Nemo enim ipsam voluptatem quia voluptas sit aspernatur aut odit aut fugit, sed quia consequuntur magni dolores eos qui ratione voluptatem sequi nesciunt.</p>
    <span class="btn">Read More <svg viewBox="0 0 16 16"><circle cx="8" cy="8" r="7" fill="#fff"/><path d="M6 4l4 4-4 4" stroke="#e2135b" stroke-width="2" fill="none"/></svg></span>
  </div>
  <svg class="about-photo" viewBox="0 0 540 530" role="img" aria-label="A driver in a shirt and tie standing beside the cab of a white lorry">
    <defs><linearGradient id="aboutTone" x1="0" y1="0" x2="0" y2="1"><stop offset="0" stop-color="#dfe6ea"/><stop offset=".55" stop-color="#b9c1c6"/><stop offset="1" stop-color="#5f6568"/></linearGradient></defs>
    <polygon points="30,0 540,0 540,530 0,530" fill="url(#aboutTone)"/>
    <polygon points="30,0 50,0 20,530 0,530" fill="#e2135b"/>
  </svg>
</section>

<section class="what-we-do">
  <div class="wwd-frame"></div>
  <div class="wwd-photo" role="img" aria-label="Two white and maroon lorries parked on a yard"></div>
  <div class="wwd-copy">
    <h2>What We Do</h2>
    <p class="body-copy">Lorem ipsum dolor sit amet, consectetur adipiscing elit, sed do eiusmod tempor incididunt ut labore et dolore magna aliqua. Quis ipsum suspendisse ultrices gravida. Risus commodo viverra maecenas accumsan lacus vel facilisis. Lorem ipsum dolor sit amet, consectetur adipiscing elit, sed do eiusmod tempor incididunt ut labore et dolore magna aliqua.</p>
    <span class="btn">Read More <svg viewBox="0 0 16 16"><circle cx="8" cy="8" r="7" fill="#fff"/><path d="M6 4l4 4-4 4" stroke="#e2135b" stroke-width="2" fill="none"/></svg></span>
  </div>
</section>

<section class="serve">
  <h2>Where We Serve</h2>
  <ul class="serve-list">
    <li><svg viewBox="0 0 16 20"><path d="M8 0a7 7 0 0 0-7 7c0 5 7 13 7 13s7-8 7-13a7 7 0 0 0-7-7z" fill="#fff"/><circle cx="8" cy="7" r="2.5" fill="#e2135b"/></svg>Lorem Ipsum</li>
    <li><svg viewBox="0 0 16 20"><path d="M8 0a7 7 0 0 0-7 7c0 5 7 13 7 13s7-8 7-13a7 7 0 0 0-7-7z" fill="#fff"/><circle cx="8" cy="7" r="2.5" fill="#e2135b"/></svg>Lorem Ipsum</li>
    <li><svg viewBox="0 0 16 20"><path d="M8 0a7 7 0 0 0-7 7c0 5 7 13 7 13s7-8 7-13a7 7 0 0 0-7-7z" fill="#fff"/><circle cx="8" cy="7" r="2.5" fill="#e2135b"/></svg>Lorem Ipsum</li>
    <li><svg viewBox="0 0 16 20"><path d="M8 0a7 7 0 0 0-7 7c0 5 7 13 7 13s7-8 7-13a7 7 0 0 0-7-7z" fill="#fff"/><circle cx="8" cy="7" r="2.5" fill="#e2135b"/></svg>Lorem Ipsum</li>
    <li><svg viewBox="0 0 16 20"><path d="M8 0a7 7 0 0 0-7 7c0 5 7 13 7 13s7-8 7-13a7 7 0 0 0-7-7z" fill="#fff"/><circle cx="8" cy="7" r="2.5" fill="#e2135b"/></svg>Lorem Ipsum</li>
    <li><svg viewBox="0 0 16 20"><path d="M8 0a7 7 0 0 0-7 7c0 5 7 13 7 13s7-8 7-13a7 7 0 0 0-7-7z" fill="#fff"/><circle cx="8" cy="7" r="2.5" fill="#e2135b"/></svg>Lorem Ipsum</li>
    <li><svg viewBox="0 0 16 20"><path d="M8 0a7 7 0 0 0-7 7c0 5 7 13 7 13s7-8 7-13a7 7 0 0 0-7-7z" fill="#fff"/><circle cx="8" cy="7" r="2.5" fill="#e2135b"/></svg>Lorem Ipsum</li>
    <li><svg viewBox="0 0 16 20"><path d="M8 0a7 7 0 0 0-7 7c0 5 7 13 7 13s7-8 7-13a7 7 0 0 0-7-7z" fill="#fff"/><circle cx="8" cy="7" r="2.5" fill="#e2135b"/></svg>Lorem Ipsum</li>
    <li><svg viewBox="0 0 16 20"><path d="M8 0a7 7 0 0 0-7 7c0 5 7 13 7 13s7-8 7-13a7 7 0 0 0-7-7z" fill="#fff"/><circle cx="8" cy="7" r="2.5" fill="#e2135b"/></svg>Lorem Ipsum</li>
    <li><svg viewBox="0 0 16 20"><path d="M8 0a7 7 0 0 0-7 7c0 5 7 13 7 13s7-8 7-13a7 7 0 0 0-7-7z" fill="#fff"/><circle cx="8" cy="7" r="2.5" fill="#e2135b"/></svg>Lorem Ipsum</li>
    <li><svg viewBox="0 0 16 20"><path d="M8 0a7 7 0 0 0-7 7c0 5 7 13 7 13s7-8 7-13a7 7 0 0 0-7-7z" fill="#fff"/><circle cx="8" cy="7" r="2.5" fill="#e2135b"/></svg>Lorem Ipsum</li>
    <li><svg viewBox="0 0 16 20"><path d="M8 0a7 7 0 0 0-7 7c0 5 7 13 7 13s7-8 7-13a7 7 0 0 0-7-7z" fill="#fff"/><circle cx="8" cy="7" r="2.5" fill="#e2135b"/></svg>Lorem Ipsum</li>
  </ul>
  <div class="serve-map" role="img" aria-label="World map showing the regions served"></div>
</section>

<section class="contact">
  <h2 class="section-title">Contact Us</h2>
  <div class="contact-form">
    <div class="field" style="top:0">Name</div>
    <div class="field" style="top:72px">Email Address</div>
    <div class="field" style="top:144px">Phone Number</div>
    <div class="field message">Message</div>
  </div>
  <span class="btn">Submit <svg viewBox="0 0 16 16"><circle cx="8" cy="8" r="7" fill="#fff"/><path d="M6 4l4 4-4 4" stroke="#e2135b" stroke-width="2" fill="none"/></svg></span>
</section>

<footer class="site-footer">
  <div class="footer-brand">Garvel Pryce Transport</div>
  <nav class="footer-nav"><span>Home</span><span>About Us</span><span>Services</span><span>What We Do</span><span>Testimonials</span><span>Gallery</span><span>Contact</span></nav>
  <div class="footer-rule"></div>
  <p class="footer-copy">© 2024 Garvel Pryce Transport. All rights reserved.</p>
</footer>

</body>
</html>
```